Australian Trucking Company Requires Professional Looking Stationary

We require a professional looking stationary design that incorporates our newly designed logo.

Our business, called "Brell Haulage Contracting", provides contracting work, transport and logistics to business in Western Australia particularly with links to the mining sector.

We are a small business looking to expand and our new logo and our new stationary will help develop our brand image in our market place.

Target Market(s)

Businesses and Corporation with links to the Mining Sector

Industry/Entity Type

Small Business

Requirements
Must have
• The letterhead must have the following details:
The new logo

Text saying: "Brell Holdings Pty Ltd (ACN 582 316 907) ATF The Brell Discretionary Trust T/AS"
"ABN 71 834 209 553"
Address "P.O Box 817 Wattlegrove WA, 6958"
Phone: 08 9352 7140
Email: brellhaul@mailbox-example.com.au

The text on the letterhead should be editable as the details are likely to change in the near future. Provision should be made for a website address all though one isn't available at the moment.

The styling, layout and font text is entirely up to the designer.

```html
<!DOCTYPE html>
<html lang="en">
<head>
<meta charset="utf-8">
<title>Brell Haulage Contracting – Letterhead</title>
<link href="https://fonts.googleapis.com/css2?family=Roboto:wght@400;900&display=swap" rel="stylesheet">
<style>
  :root {
    --brand-red: #c8202a;
    --deep-red: #8a1419;
    --band-red: #7d1216;
    --ink: #3d3d3d;
    --rule-black: #1a1a1a;
    --silver: #c9c9c9;
    --paper: #ffffff;
    --truck-grey: #9a9a9a;
  }
  * { margin: 0; padding: 0; box-sizing: border-box; }
  html, body { width: 921px; height: 1200px; overflow: hidden; background: var(--paper); }
  .letterhead {
    position: relative;
    width: 921px;
    height: 1200px;
    background: var(--paper);
    font-family: "Roboto", Arial, sans-serif;
    overflow: hidden;
  }
  .brand {
    position: absolute;
    left: 50px;
    top: 28px;
    display: flex;
    align-items: center;
    gap: 18px;
  }
  .brand-truck {
    width: 128px;
    height: 92px;
    background: linear-gradient(180deg, #c4c4c4 0%, var(--truck-grey) 60%, #6f6f6f 100%);
    border-radius: 6px;
  }
  .brand-name {
    color: var(--brand-red);
    font-weight: 900;
    font-size: 30px;
    line-height: 30px;
    text-transform: uppercase;
    letter-spacing: 0.5px;
  }
  .contact {
    position: absolute;
    right: 40px;
    top: 22px;
    list-style: none;
    text-align: right;
    font-size: 17px;
    line-height: 29px;
    color: var(--ink);
  }
  .contact li { display: flex; justify-content: flex-end; align-items: center; gap: 12px; }
  .contact .icon { width: 14px; height: 14px; fill: var(--brand-red); flex: none; }
  .contact .abn { color: var(--deep-red); padding-right: 26px; }
  .watermark-truck {
    position: absolute;
    left: 431px;
    top: 690px;
    width: 460px;
    height: 400px;
    background: radial-gradient(closest-side at 55% 55%, rgba(200,200,200,0.45) 0%, rgba(225,225,225,0.22) 55%, rgba(255,255,255,0) 100%);
  }
  .footer-wave {
    position: absolute;
    left: 0;
    bottom: 0;
    width: 921px;
    height: 160px;
  }
  .footer-legal {
    position: absolute;
    right: 24px;
    bottom: 8px;
    color: #ffffff;
    font-size: 15.5px;
    line-height: 20px;
  }
</style>
</head>
<body>
<main class="letterhead">
  <header class="brand">
    <div class="brand-truck" role="img" aria-label="Illustration of a prime mover truck"></div>
    <div class="brand-name">Brell<br>Haulage<br>Contracting</div>
  </header>

  <ul class="contact">
    <li>08 9352 7140
      <svg class="icon" viewBox="0 0 16 16"><path d="M3 1h3l1.5 4-2 1.3a9 9 0 0 0 4.2 4.2L11 8.5l4 1.5v3a2 2 0 0 1-2 2A12 12 0 0 1 1 3a2 2 0 0 1 2-2z"/></svg>
    </li>
    <li>brellhaul@mailbox-example.com.au
      <svg class="icon" viewBox="0 0 16 16"><path d="M1 4h14v9H1z"/><path d="M1 4l7 5 7-5" fill="none" stroke="#fff" stroke-width="1.4"/></svg>
    </li>
    <li>www.brellhaulage-example.com.au
      <svg class="icon" viewBox="0 0 16 16"><circle cx="8" cy="8" r="6.5" fill="none" stroke="var(--brand-red)" stroke-width="1.6"/><circle cx="8" cy="8" r="2.5"/></svg>
    </li>
    <li>P.O Box 817 Wattlegrove WA, 6958
      <svg class="icon" viewBox="0 0 16 16"><path d="M8 1l7 7h-2v7H9.5v-4h-3v4H3V8H1z"/></svg>
    </li>
    <li class="abn">ABN 71 834 209 553</li>
  </ul>

  <div class="watermark-truck" role="img" aria-label="Faint illustration of a prime mover truck"></div>

  <svg class="footer-wave" viewBox="0 0 921 160" preserveAspectRatio="none" aria-hidden="true">
    <path d="M0,120 C260,128 420,66 620,44 S860,18 921,14" fill="none" stroke="var(--rule-black)" stroke-width="4"/>
    <path d="M0,126 C260,134 420,72 620,50 S860,24 921,20" fill="none" stroke="var(--silver)" stroke-width="4"/>
    <path d="M0,131 C260,139 420,77 620,55 S860,29 921,25 L921,160 L0,160 Z" fill="var(--band-red)"/>
    <path d="M0,140 C120,143 220,140 310,134" fill="none" stroke="var(--rule-black)" stroke-width="3" stroke-linecap="round"/>
    <path d="M0,146 C120,149 220,146 310,140" fill="none" stroke="#ffffff" stroke-width="2" stroke-linecap="round"/>
  </svg>
  <p class="footer-legal">Brell Holdings Pty Ltd (ACN 582 316 907) ATF The Brell Discretionary Trust T/AS</p>
</main>
</body>
</html>
```